Landscape design build company door flyer

I would like this flyer to convey a high-level of professionalism for a company that is excellent with communication with their clients as well as a company that does incredible installations

Went on vacation/holiday

```html
<!DOCTYPE html>
<html lang="en">
<head>
<meta charset="utf-8">
<title>Cedarcrest Builders – Door Flyer</title>
<link rel="stylesheet" href="https://fonts.googleapis.com/css2?family=Archivo+Black&family=Rajdhani:wght@600;700&family=Saira+Condensed:wght@700;800&display=swap">
<style>
  :root{
    --navy:#0e2a40;
    --orange:#f07c12;
    --white:#ffffff;
    --paper:#f6f6f6;
    --ink:#1c2630;
    --backdrop:#e6e6e6;
  }
  *{box-sizing:border-box;margin:0;padding:0}
  html,body{width:1200px;height:1029px;overflow:hidden;background:var(--backdrop)}
  .flyer{
    position:absolute;left:213px;top:16px;width:774px;height:996px;
    background:var(--paper);overflow:hidden;
  }
  .hero{
    position:absolute;left:0;top:0;width:774px;height:560px;
    background:
      linear-gradient(100deg,rgba(255,255,255,.95) 0%,rgba(255,255,255,.55) 30%,rgba(255,255,255,0) 55%),
      linear-gradient(180deg,#dfe3e4 0%,#b9b4a6 35%,#9c9a8d 55%,#5f8a3c 80%,#3f7a2a 100%);
  }
  .hero::after{
    content:"";position:absolute;right:0;top:0;width:260px;height:460px;
    background:linear-gradient(180deg,rgba(220,225,222,.8),#3f5a3a 60%,rgba(63,90,58,0));
  }
  .brand{position:absolute;left:20px;top:118px;width:190px;text-align:center}
  .brand-name{font-family:"Rajdhani",sans-serif;font-weight:700;font-size:21px;color:var(--orange);letter-spacing:.5px;line-height:1}
  .brand-tag{font-family:"Rajdhani",sans-serif;font-weight:600;font-size:9.5px;color:var(--ink);letter-spacing:.6px;margin-top:2px}
  .gallery{position:absolute;top:510px;left:68px;display:flex;gap:11px}
  .thumb{width:154px;height:124px;border:5px solid var(--white);background:var(--white)}
  .thumb span{display:block;width:100%;height:100%}
  .t1 span{background:linear-gradient(180deg,#2f4a33 0%,#3d5a3a 45%,#b8512a 60%,#5d9a3a 75%,#4f8d2f 100%)}
  .t2 span{background:linear-gradient(180deg,#8d9b86 0%,#b8bcb8 40%,#8f9598 70%,#6d7275 100%)}
  .t3 span{background:linear-gradient(180deg,#9aa1a1 0%,#8a6d4e 35%,#a07b56 60%,#b8a58a 100%)}
  .t4 span{background:linear-gradient(160deg,#c9c5b8 0%,#5d7a45 40%,#8a6a80 60%,#a7a9a8 100%)}
  .services-title{
    position:absolute;top:651px;left:0;width:774px;text-align:center;
    font-family:"Saira Condensed",sans-serif;font-weight:800;font-size:34px;color:var(--navy);line-height:1;
  }
  .rule{position:absolute;top:670px;height:2px;background:var(--ink)}
  .rule::after{content:"";position:absolute;top:-2px;width:6px;height:6px;border-radius:50%;background:var(--ink)}
  .rule-left{left:114px;width:152px}.rule-left::after{right:-3px}
  .rule-right{left:505px;width:154px}.rule-right::after{left:-3px}
  .service-list{position:absolute;top:695px;list-style:none}
  .service-list li{
    display:flex;align-items:center;gap:7px;height:18.5px;
    font-family:"Rajdhani",sans-serif;font-weight:700;font-size:21px;letter-spacing:2px;color:var(--ink);line-height:1;
  }
  .service-list svg{width:12px;height:12px;flex:none}
  .list-left{left:97px}.list-right{left:441px}
  .band{position:absolute;left:0;bottom:0;width:774px;height:176px}
  .cta{position:absolute;left:56px;top:876px;color:var(--white)}
  .cta-note{font-family:"Saira Condensed",sans-serif;font-weight:700;font-size:9.5px;letter-spacing:.2px}
  .cta-line{font-family:"Archivo Black",sans-serif;color:var(--orange);font-size:11.5px;letter-spacing:.6px;line-height:1.1}
  .cta-line.big{font-size:14px}
  .phone{position:absolute;left:56px;top:920px;display:flex;align-items:center;gap:10px;
    font-family:"Saira Condensed",sans-serif;font-weight:800;font-size:36px;color:var(--white);line-height:1;letter-spacing:.5px}
  .address{position:absolute;left:56px;top:961px;display:flex;align-items:center;gap:10px;
    font-family:"Saira Condensed",sans-serif;font-weight:700;font-size:10.5px;letter-spacing:2.2px;color:var(--orange)}
  .email{position:absolute;right:71px;top:961px;font-family:"Saira Condensed",sans-serif;font-weight:700;font-size:11px;color:var(--white)}
</style>
</head>
<body>
<main class="flyer">
  <div class="hero" role="img" aria-label="Photo of a two-level wooden deck with staircase and grey lower platform beside a house, lawn and tall evergreens"></div>

  <div class="brand">
    <div class="brand-name">CEDARCREST BUILDERS</div>
    <div class="brand-tag">OUTDOOR LIVING SPACES</div>
  </div>

  <div class="gallery">
    <div class="thumb t1"><span role="img" aria-label="Photo of a cabin with a red-stained wraparound deck in a forest clearing"></span></div>
    <div class="thumb t2"><span role="img" aria-label="Photo of a grey composite deck with black metal railing"></span></div>
    <div class="thumb t3"><span role="img" aria-label="Photo of a tiered brown composite platform deck on gravel"></span></div>
    <div class="thumb t4"><span role="img" aria-label="Photo of a landscaped hillside garden with stone retaining walls and steps"></span></div>
  </div>

  <div class="rule rule-left"></div>
  <h2 class="services-title">OUR SERVICES</h2>
  <div class="rule rule-right"></div>

  <ul class="service-list list-left">
    <li><svg viewBox="0 0 12 12"><circle cx="6" cy="6" r="6" fill="#f07c12"/><path d="M3.2 6.2l1.9 1.9 3.7-3.9" stroke="#fff" stroke-width="1.7" fill="none"/></svg>LANDSCAPE DESIGN</li>
    <li><svg viewBox="0 0 12 12"><circle cx="6" cy="6" r="6" fill="#f07c12"/><path d="M3.2 6.2l1.9 1.9 3.7-3.9" stroke="#fff" stroke-width="1.7" fill="none"/></svg>LANDSCAPING</li>
    <li><svg viewBox="0 0 12 12"><circle cx="6" cy="6" r="6" fill="#f07c12"/><path d="M3.2 6.2l1.9 1.9 3.7-3.9" stroke="#fff" stroke-width="1.7" fill="none"/></svg>HARDSCAPING</li>
    <li><svg viewBox="0 0 12 12"><circle cx="6" cy="6" r="6" fill="#f07c12"/><path d="M3.2 6.2l1.9 1.9 3.7-3.9" stroke="#fff" stroke-width="1.7" fill="none"/></svg>RETAINING WALL DESIGN</li>
    <li><svg viewBox="0 0 12 12"><circle cx="6" cy="6" r="6" fill="#f07c12"/><path d="M3.2 6.2l1.9 1.9 3.7-3.9" stroke="#fff" stroke-width="1.7" fill="none"/></svg>FENCING</li>
    <li><svg viewBox="0 0 12 12"><circle cx="6" cy="6" r="6" fill="#f07c12"/><path d="M3.2 6.2l1.9 1.9 3.7-3.9" stroke="#fff" stroke-width="1.7" fill="none"/></svg>POOL DESIGNS</li>
    <li><svg viewBox="0 0 12 12"><circle cx="6" cy="6" r="6" fill="#f07c12"/><path d="M3.2 6.2l1.9 1.9 3.7-3.9" stroke="#fff" stroke-width="1.7" fill="none"/></svg>DRIVEWAYS</li>
  </ul>
  <ul class="service-list list-right">
    <li><svg viewBox="0 0 12 12"><circle cx="6" cy="6" r="6" fill="#f07c12"/><path d="M3.2 6.2l1.9 1.9 3.7-3.9" stroke="#fff" stroke-width="1.7" fill="none"/></svg>PAVERS</li>
    <li><svg viewBox="0 0 12 12"><circle cx="6" cy="6" r="6" fill="#f07c12"/><path d="M3.2 6.2l1.9 1.9 3.7-3.9" stroke="#fff" stroke-width="1.7" fill="none"/></svg>DECK DESIGNS</li>
    <li><svg viewBox="0 0 12 12"><circle cx="6" cy="6" r="6" fill="#f07c12"/><path d="M3.2 6.2l1.9 1.9 3.7-3.9" stroke="#fff" stroke-width="1.7" fill="none"/></svg>LUXURY OUTDOOR</li>
    <li><svg viewBox="0 0 12 12"><circle cx="6" cy="6" r="6" fill="#f07c12"/><path d="M3.2 6.2l1.9 1.9 3.7-3.9" stroke="#fff" stroke-width="1.7" fill="none"/></svg>SHEDS</li>
    <li><svg viewBox="0 0 12 12"><circle cx="6" cy="6" r="6" fill="#f07c12"/><path d="M3.2 6.2l1.9 1.9 3.7-3.9" stroke="#fff" stroke-width="1.7" fill="none"/></svg>PATIO DESIGNS</li>
    <li><svg viewBox="0 0 12 12"><circle cx="6" cy="6" r="6" fill="#f07c12"/><path d="M3.2 6.2l1.9 1.9 3.7-3.9" stroke="#fff" stroke-width="1.7" fill="none"/></svg>OUTDOOR LIGHTING</li>
    <li><svg viewBox="0 0 12 12"><circle cx="6" cy="6" r="6" fill="#f07c12"/><path d="M3.2 6.2l1.9 1.9 3.7-3.9" stroke="#fff" stroke-width="1.7" fill="none"/></svg>FIREPLACES</li>
  </ul>

  <svg class="band" viewBox="0 0 774 176" preserveAspectRatio="none" aria-hidden="true">
    <polygon points="0,1 774,65 774,176 0,176" fill="#f07c12"/>
    <polygon points="0,13 774,77 774,176 0,176" fill="#0e2a40"/>
  </svg>

  <div class="cta">
    <p class="cta-note">WE OFFER A LARGE RANGE OF SERVICES NOT LISTED SO</p>
    <p class="cta-line">CALL US TODAY FOR A PERSONALISED</p>
    <p class="cta-line big">QUOTE TO SUIT YOUR NEEDS</p>
  </div>

  <div class="phone">
    <svg width="16" height="26" viewBox="0 0 16 26" aria-hidden="true"><rect x="1.5" y="1.5" width="13" height="23" rx="2" fill="none" stroke="#fff" stroke-width="3"/></svg>
    555-201-4386
  </div>

  <div class="address">
    <svg width="13" height="19" viewBox="0 0 13 19" aria-hidden="true"><path d="M6.5 0A6.5 6.5 0 0 0 0 6.5C0 11 6.5 19 6.5 19S13 11 13 6.5A6.5 6.5 0 0 0 6.5 0z" fill="#fff"/><circle cx="6.5" cy="6.5" r="2.4" fill="#0e2a40"/></svg>
    1820 NE ALDER LANE REDMONT, WA 98000
  </div>

  <div class="email">info@cedarcrestbuilders.com</div>
</main>
</body>
</html>
```